Kelvaro.ch is looking for business card letterhead and envelope C5 with WOW effect

We need a strong business card for our company Kelvaro.ch, logo is available. You want a black or dark background on which the logo Stark r% 26 # 252; appears. Letterhead and envelope in C5 format should be in a similar design, but does not have to be We need a strong business card for our company Kelvaro.ch, logo is available. A black or dark background is desired, on which the logo Stark comes across. The letterhead and the envelope in C5 format should have a similar design.

Target Market(s)

Private customers as well as entrepreneurs

Contact Information for Business Card

E-mail: info@kelvaro-example.ch
Web.www.Kelvaro-example.ch
Tel: +41 ( 0 ) 79 482 6037
Adresse:
Lindenweg 14
9406 Tarnbach

Hier kann man Icons verwenden für Email,Tel und Adressse

Font styles to use
Other font styles liked:
• Dubai,bold

Colors

Designer to choose colors to be used in the design.

Requirements
Must have
• WOW effect
Nice to have
• R% 26 # 252; back business card with our service listings. - VEHICLE LABELING - SHOP WINDOW LABELING - STICKERS AND MUCH MORE ... in red color

```html
<!DOCTYPE html>
<html lang="en">
<head>
<meta charset="utf-8">
<title>Kelvaro.ch – Business Card</title>
<link rel="stylesheet" href="https://fonts.googleapis.com/css2?family=Arimo:wght@400&family=Mukta:wght@700;800&display=swap">
<style>
  :root {
    --backdrop: #cdcdcd;
    --card-black: #060606;
    --brand-yellow: #ffcb1f;
    --brand-yellow-deep: #e0a800;
    --text-light: #f2f2f2;
    --text-dark: #0a0a0a;
  }
  * { margin: 0; padding: 0; box-sizing: border-box; }
  html, body {
    width: 1200px; height: 802px; overflow: hidden;
    background: var(--backdrop);
  }
  .stage { position: relative; width: 1200px; height: 802px; }

  .card {
    position: absolute; top: 274px;
    width: 442px; height: 264px; overflow: hidden;
  }
  .card--front { left: 136px; background: var(--card-black); }
  .card--back  { left: 625px; background: var(--brand-yellow); }

  .brand-name {
    position: absolute;
    font-family: "Mukta", sans-serif; font-weight: 800;
    text-transform: uppercase; letter-spacing: 0.6px;
    line-height: 1; white-space: nowrap;
  }
  .card--front .brand-name {
    left: 23px; top: 42px; font-size: 33px; color: var(--brand-yellow);
  }
  .card--back .brand-name {
    left: 173px; top: 84px; font-size: 34px; color: var(--text-dark);
  }
  .brand-square {
    position: absolute; left: 124px; top: 88px;
    width: 30px; height: 30px; background: var(--text-dark);
  }

  .contact-list {
    position: absolute; left: 24px; top: 141px; list-style: none;
    font-family: "Arimo", sans-serif; font-size: 12.5px; color: var(--text-light);
  }
  .contact-list li {
    display: flex; align-items: center; gap: 6px; height: 18.5px;
  }
  .contact-icon { width: 15px; height: 15px; flex: none; }

  .address {
    position: absolute; left: 26px; top: 215px;
    font-family: "Arimo", sans-serif; font-size: 12.5px; color: var(--text-light);
    white-space: nowrap;
  }

  .decor-area {
    position: absolute; left: 240px; top: 22px; width: 202px; height: 240px;
    background:
      radial-gradient(ellipse 55% 30% at 60% 78%, var(--brand-yellow) 0%, rgba(255,203,31,0) 100%),
      radial-gradient(ellipse 45% 35% at 48% 35%, var(--brand-yellow) 0%, rgba(255,203,31,0) 100%),
      radial-gradient(ellipse 60% 55% at 58% 55%, var(--brand-yellow-deep) 0%, rgba(224,168,0,0.35) 55%, rgba(6,6,6,0) 100%);
  }

  .services {
    position: absolute; left: 0; right: 0; top: 215px; text-align: center;
    font-family: "Mukta", sans-serif; font-weight: 700; font-size: 12.5px;
    line-height: 14.5px; color: var(--text-dark); text-transform: uppercase;
  }
</style>
</head>
<body>
<main class="stage">

  <section class="card card--front" aria-label="Business card front">
    <div class="brand-name">Kelvaro.ch</div>

    <ul class="contact-list">
      <li>
        <svg class="contact-icon" viewBox="0 0 16 16" aria-hidden="true">
          <rect x="1" y="1" width="14" height="14" rx="2" fill="none" stroke="var(--brand-yellow)" stroke-width="1.5"/>
          <path d="M5 4.2c.5-.4 1-.3 1.3.2l.7 1.3c.2.4.1.8-.2 1l-.5.4c.4.9 1.1 1.7 2 2.1l.4-.5c.3-.3.7-.4 1-.2l1.3.7c.5.3.6.8.2 1.3l-.6.7c-.5.5-1.3.6-2 .3C6.6 10.6 5.2 9.2 4.4 7.2c-.3-.7-.2-1.5.3-2z" fill="var(--brand-yellow)"/>
        </svg>
        <span>+41 ( 0 ) 79 482 6037</span>
      </li>
      <li>
        <svg class="contact-icon" viewBox="0 0 16 16" aria-hidden="true">
          <rect x="0.5" y="3" width="15" height="10" fill="var(--brand-yellow)"/>
          <path d="M0.5 3.5 8 9l7.5-5.5" fill="none" stroke="var(--card-black)" stroke-width="1.2"/>
        </svg>
        <span>info@kelvaro-example.ch</span>
      </li>
      <li>
        <svg class="contact-icon" viewBox="0 0 16 16" aria-hidden="true">
          <g fill="none" stroke="var(--brand-yellow)" stroke-width="1.3">
            <circle cx="8" cy="8" r="6.8"/>
            <ellipse cx="8" cy="8" rx="3" ry="6.8"/>
            <path d="M1.2 8h13.6M2.2 4.6h11.6M2.2 11.4h11.6"/>
          </g>
        </svg>
        <span>www.Kelvaro-example.ch</span>
      </li>
    </ul>

    <p class="address">Lindenweg 14,9406 Tarnbach</p>

    <div class="decor-area" role="img" aria-label="Yellow honeycomb decoration area"></div>
  </section>

  <section class="card card--back" aria-label="Business card back">
    <div class="brand-square" aria-hidden="true"></div>
    <div class="brand-name">Kelvaro.ch</div>
    <p class="services">Vehicle labeling | Shop window labeling<br>Stickers and much more ...</p>
  </section>

</main>
</body>
</html>
```